New Alcoholic Spiked Seltzer Line

We need a can design for a line of low calorie alcoholic seltzer. This product is a sparkling water and vodka drink with no sugar added in a slim 12 oz can.

This is a lighter, healthier, alternative to the sugary ready-to-drinks on the market. The product contains only 3 ingredients: Vodka, Water and Natural Flavors. It has only 100 calories but still has 5% alcohol, so you don't need to sacrifice alcohol to cut calories.

This product also does not contain any preservatives.

We want this design to communicate the following objectives to the consumer and in this order:

1. Appetizing product
2.Low calorie
3.Communicate the type of beverage (Spiked Seltzer)

The brand name of the product is VELKA.

The flavor of the product needed to be used for the design is Mango-Orange.

Comparable products are:

www.brindlefizzworks.example/
https://www.quorvabubbles.example
https://pelnavo.example/

The designs should not infringe or copy the creative directions of the products mentionned above. They are only given so that you can better understand the type of product we are developing.

Target Market(s)

Young Professional women between the ages of 25 and 44

Industry/Entity Type

Product

Colors

Designer to choose colors to be used in the design.

Requirements
Must have
• Design extendibility, meaning it can be adapted for other flavors.
• This is a new category in the market we are targeting, so consumers must easily be able to identify what type of product this is.

```html
<!DOCTYPE html>
<html lang="en">
<head>
<meta charset="utf-8">
<title>VELKA Spiked Seltzer – Mango-Orange</title>
<link rel="stylesheet" href="https://fonts.googleapis.com/css2?family=Oswald:wght@500&family=Josefin+Sans:wght@300&family=Boogaloo&display=swap">
<style>
  :root {
    --bg: #ececec;
    --label: #f6f7f8;
    --label-edge: #dfe2e6;
    --band-red: #e8402c;
    --band-orange: #f07a3a;
    --band-line: #ffffff;
    --ink: #3b3f45;
    --brand-ink: #2e3338;
    --tag: #ee7a45;
    --ice-light: #dfe5f2;
    --ice-deep: #5d6aa0;
  }
  * { box-sizing: border-box; margin: 0; padding: 0; }
  html, body { width: 968px; height: 1200px; overflow: hidden; }
  body {
    background: var(--bg);
    display: flex;
    align-items: center;
    justify-content: center;
  }
  .can-label {
    position: relative;
    width: 440px;
    height: 1000px;
    background: linear-gradient(90deg, var(--label-edge), var(--label) 30%, #ffffff 55%, var(--label-edge));
    overflow: hidden;
  }
  .info-band {
    position: absolute;
    top: 30px;
    left: 0;
    width: 100%;
    height: 100px;
    background: linear-gradient(180deg, var(--band-orange), var(--band-red));
    border-top: 3px solid var(--band-line);
    border-bottom: 3px solid var(--band-line);
    box-shadow: 0 -4px 0 var(--band-red), 0 4px 0 var(--band-red);
    display: flex;
    align-items: center;
    justify-content: center;
    gap: 18px;
    white-space: nowrap;
    font-family: 'Oswald', sans-serif;
    color: #fff;
  }
  .info-band .minor { font-size: 22px; letter-spacing: 0.5px; }
  .info-band .abv { font-size: 44px; }
  .category {
    position: absolute;
    top: 170px;
    width: 100%;
    text-align: center;
    font-family: 'Oswald', sans-serif;
    font-size: 50px;
    color: var(--ink);
    letter-spacing: 0.5px;
  }
  .ice-art {
    position: absolute;
    right: 0;
    top: 500px;
    width: 260px;
    height: 500px;
    background: radial-gradient(ellipse at 60% 45%, var(--ice-light), #b7c0dc 45%, var(--ice-deep) 85%, transparent 100%);
    opacity: 0.75;
    border-radius: 60% 0 0 40%;
  }
  .brand-name {
    position: absolute;
    left: 50%;
    top: 540px;
    transform: translate(-50%, -50%) rotate(-58deg);
    font-family: 'Josefin Sans', sans-serif;
    font-weight: 300;
    font-size: 170px;
    letter-spacing: 6px;
    color: var(--brand-ink);
    white-space: nowrap;
  }
  .flavor-tag {
    position: absolute;
    left: 50%;
    top: 870px;
    transform: translateX(-50%);
    width: 370px;
    height: 72px;
    background: var(--tag);
    border-radius: 6px 14px 8px 12px;
    display: flex;
    align-items: center;
    justify-content: center;
    font-family: 'Boogaloo', sans-serif;
    font-size: 50px;
    color: #fff;
  }
</style>
</head>
<body>
  <main class="can-label">
    <div class="info-band">
      <span class="minor">100 CALORIES</span>
      <span class="abv">5% ALC/VOL</span>
      <span class="minor">100 CALORIES</span>
    </div>
    <h2 class="category">SPIKED SELTZER</h2>
    <div class="ice-art" role="img" aria-label="Photo of clear ice cubes stacked along the right side of the can"></div>
    <h1 class="brand-name">VELKA</h1>
    <div class="flavor-tag">Mango-Orange</div>
  </main>
</body>
</html>
```